Agriculture Security Company needs a business card design

We need a business card design for a new company based in Seattle calls Ferncrest Guardline LLC. We provide high-end physical security solutions that is geared and focused towards to the marijuana grow operations, wholesalers and distributors. We DO NOT get involved in the retail operations (store fronts). We would like to see designs that incorporate professionalism, reliability, trustworthy and forward thinking as traits of our organization.

Industry/Entity Type

Security

```html
<!DOCTYPE html>
<html lang="en">
<head>
<meta charset="utf-8">
<title>Ferncrest Guardline LLC – Business Card</title>
<link rel="stylesheet" href="https://fonts.googleapis.com/css2?family=Open+Sans:wght@400;600;700&display=swap">
<style>
  :root {
    --bg: #e9e6e0;
    --card: #ffffff;
    --card-shade: #eeeeee;
    --green-dark: #1f7a3f;
    --green-light: #7cb342;
    --text-grey: #444444;
    --muted: #6b6b6b;
  }
  * { margin: 0; padding: 0; box-sizing: border-box; }
  html, body { width: 1200px; height: 1023px; overflow: hidden; }
  body {
    background: var(--bg);
    font-family: "Open Sans", Arial, sans-serif;
    position: relative;
  }
  .card {
    position: absolute;
    width: 580px;
    height: 330px;
    border-radius: 14px;
    background: linear-gradient(135deg, var(--card) 0%, var(--card-shade) 100%);
    box-shadow: 0 10px 28px rgba(0,0,0,0.22);
    overflow: hidden;
  }
  .card-front { left: 70px; top: 110px; }
  .card-back { left: 550px; top: 580px; }

  /* front */
  .front-band {
    position: absolute; left: 0; right: 0; bottom: 0; height: 30px;
    background: var(--green-dark);
  }
  .address-pill {
    position: absolute; right: 0; bottom: 14px;
    height: 40px; padding: 0 26px 0 30px;
    background: var(--green-light);
    border-radius: 20px 0 0 20px;
    color: #fff; font-size: 14px; line-height: 40px;
  }
  .front-brand {
    position: absolute; left: 44px; top: 110px; width: 250px;
    display: flex; align-items: center; gap: 10px;
  }
  .brand-dot {
    flex: none; width: 14px; height: 14px; border-radius: 50%;
    background: var(--green-light);
  }
  .brand-name {
    font-weight: 700; color: var(--green-dark);
    font-size: 24px; line-height: 1.15;
  }
  .person { position: absolute; left: 150px; top: 220px; text-align: right; width: 150px; }
  .person-name { font-size: 21px; font-weight: 700; color: var(--green-dark); }
  .person-title { font-size: 14px; color: var(--green-light); }
  .divider {
    position: absolute; left: 322px; top: 120px; width: 1px; height: 140px;
    background: linear-gradient(to bottom, transparent, #bbbbbb, transparent);
  }
  .contact-list {
    position: absolute; left: 342px; top: 140px; list-style: none;
    font-size: 14px; color: var(--text-grey);
  }
  .contact-list li { display: flex; align-items: center; gap: 9px; margin-bottom: 10px; }
  .contact-list svg { width: 14px; height: 14px; flex: none; fill: var(--green-dark); }

  /* back */
  .back-brand {
    position: absolute; left: 0; right: 0; top: 140px;
    display: flex; justify-content: center; align-items: center; gap: 12px;
  }
  .back-brand .brand-name { font-size: 30px; }
  .back-web {
    position: absolute; left: 40px; top: 165px;
    transform: translate(-50%, -50%) rotate(90deg);
    font-size: 13px; letter-spacing: 3px; color: var(--muted); white-space: nowrap;
  }
</style>
</head>
<body>
  <section class="card card-front">
    <div class="front-brand">
      <span class="brand-dot"></span>
      <span class="brand-name">Ferncrest Guardline</span>
    </div>
    <div class="person">
      <p class="person-name">Dana Whitlow</p>
      <p class="person-title">President</p>
    </div>
    <div class="divider"></div>
    <ul class="contact-list">
      <li><svg viewBox="0 0 24 24"><path d="M6.6 10.8a15.1 15.1 0 0 0 6.6 6.6l2.2-2.2a1 1 0 0 1 1-.25 11.4 11.4 0 0 0 3.6.57 1 1 0 0 1 1 1V20a1 1 0 0 1-1 1A17 17 0 0 1 3 4a1 1 0 0 1 1-1h3.5a1 1 0 0 1 1 1c0 1.25.2 2.45.57 3.57a1 1 0 0 1-.25 1z"/></svg>555-014-2287</li>
      <li><svg viewBox="0 0 24 24"><path d="M2 5h20v14H2z M2 5l10 8 10-8" stroke="#fff" stroke-width="1.5"/></svg>info@ferncrestguardline.com</li>
      <li><svg viewBox="0 0 24 24"><circle cx="12" cy="12" r="10"/><path d="M2 12h20M12 2c3 3 3 17 0 20M12 2c-3 3-3 17 0 20" stroke="#fff" stroke-width="1.3" fill="none"/></svg>www.ferncrestguardline.com</li>
    </ul>
    <div class="front-band"></div>
    <div class="address-pill">1820 Harbor Crest Ave Seattle</div>
  </section>

  <section class="card card-back">
    <p class="back-web">www.ferncrestguardline.com</p>
    <div class="back-brand">
      <span class="brand-dot"></span>
      <span class="brand-name">Ferncrest Guardline</span>
    </div>
  </section>
</body>
</html>
```